Road Construction Company needs business cards

We would like a new business card designed for our business.

We're a road construction company based in Qld, Australia.

Can the business card please have the following information on it.

Name: Warren Halbeck
Position: General Manager
Phone: 0472 915 348
Email: Warren.halbeck@tovrin.com.au
Address: 87 Marrow Ave, Pendlebay, QLD, 4023
Website: www.tovrin.com.au

Visually we'd like the card to be professional and simple.

Attached is our logo.

Our website is www.tovrin.com.au

Target Market(s)

Men aged 25-60

Contact Information for Business Card

As listed in project description

Font styles to use
Serif

Requirements
Must have
• Large logo on back of card

```html
<!DOCTYPE html>
<html lang="en">
<head>
<meta charset="utf-8">
<title>Tovrin Business Card</title>
<link rel="stylesheet" href="https://fonts.googleapis.com/css2?family=Montserrat:wght@400;500;700;800&display=swap">
<style>
  :root {
    --stage: #e6e6e4;
    --brand-blue: #0d4f9e;
    --brand-blue-light: #1466b5;
    --brand-blue-deep: #0a4590;
    --panel-white: #ebebeb;
    --ink-white: #ffffff;
    --ink-soft: #e4ecf7;
  }
  * { box-sizing: border-box; margin: 0; padding: 0; }
  html, body {
    width: 1200px; height: 1200px; overflow: hidden;
    background: var(--stage);
    font-family: "Montserrat", sans-serif;
  }
  .canvas { position: relative; width: 1200px; height: 1200px; }

  .card {
    position: absolute; left: 234px; width: 731px; height: 417px;
    overflow: hidden;
  }
  .card--front { top: 160px; }
  .card--back { top: 632px; display: flex; }

  .front-pattern {
    position: absolute; inset: 0;
    background: linear-gradient(120deg, var(--brand-blue-deep) 0%, var(--brand-blue) 45%, var(--brand-blue-light) 100%);
  }
  .front-wordmark {
    position: absolute; left: 0; right: 0; top: 50%;
    transform: translateY(-50%);
    text-align: center;
    font-weight: 800; font-size: 46px; letter-spacing: 1px;
    color: var(--ink-white);
  }

  .back-logo-panel {
    width: 255px; height: 100%;
    background: linear-gradient(160deg, #f0f0f0, #e2e2e2);
    position: relative;
  }
  .back-wordmark {
    position: absolute; left: 50%; top: 50%;
    transform: translate(-50%, -50%) rotate(-90deg);
    font-weight: 800; font-size: 50px; letter-spacing: 1px;
    color: var(--brand-blue);
    white-space: nowrap;
  }

  .back-info-panel {
    flex: 1; height: 100%;
    background: linear-gradient(135deg, var(--brand-blue-light) 0%, var(--brand-blue) 45%, var(--brand-blue-deep) 100%);
    padding: 68px 0 0 86px;
    color: var(--ink-white);
  }
  .person-name { font-weight: 700; font-size: 31px; line-height: 1.2; }
  .person-title { font-weight: 400; font-size: 18px; margin-top: 4px; color: var(--ink-soft); }
  .address { margin-top: 68px; font-size: 18px; line-height: 27px; color: var(--ink-soft); }
  .contact-list { list-style: none; margin-top: 13px; font-size: 18px; color: var(--ink-soft); }
  .contact-list li { display: flex; align-items: center; height: 28px; }
  .contact-list svg { width: 16px; height: 16px; margin-right: 9px; fill: var(--ink-white); flex: none; }
</style>
</head>
<body>
<main class="canvas">
  <section class="card card--front">
    <div class="front-pattern" role="img" aria-label="Embossed pattern of repeating chevron arrows in blue"></div>
    <div class="front-wordmark">TOVRIN</div>
  </section>

  <section class="card card--back">
    <div class="back-logo-panel">
      <div class="back-wordmark">TOVRIN</div>
    </div>
    <div class="back-info-panel">
      <h1 class="person-name">Warren Halbeck</h1>
      <p class="person-title">General Manager</p>
      <p class="address">87 Marrow Ave, Pendlebay,<br>QLD, 4023</p>
      <ul class="contact-list">
        <li>
          <svg viewBox="0 0 24 24" aria-hidden="true"><path d="M6.6 10.8a15.1 15.1 0 0 0 6.6 6.6l2.2-2.2a1 1 0 0 1 1-.25 11.4 11.4 0 0 0 3.6.57 1 1 0 0 1 1 1V20a1 1 0 0 1-1 1A17 17 0 0 1 3 4a1 1 0 0 1 1-1h3.5a1 1 0 0 1 1 1c0 1.25.2 2.45.57 3.57a1 1 0 0 1-.25 1z"/></svg>
          0472 915 348
        </li>
        <li>
          <svg viewBox="0 0 24 24" aria-hidden="true"><path d="M2 5h20v14H2z M3.5 6.5 12 13l8.5-6.5" fill="none" stroke="#fff" stroke-width="0"/><path d="M2 5h20v14H2V5zm2 2v.3l8 5.7 8-5.7V7H4z"/></svg>
          Warren.halbeck@tovrin.com.au
        </li>
        <li>
          <svg viewBox="0 0 24 24" aria-hidden="true"><path d="M12 2a10 10 0 1 0 0 20 10 10 0 0 0 0-20zm6.9 6h-3a15.7 15.7 0 0 0-1.4-3.6A8 8 0 0 1 18.9 8zM12 4a14 14 0 0 1 1.9 4h-3.8A14 14 0 0 1 12 4zM4.3 14a8 8 0 0 1 0-4h3.4a16.5 16.5 0 0 0 0 4H4.3zm.8 2h3a15.7 15.7 0 0 0 1.4 3.6A8 8 0 0 1 5.1 16zm3-8h-3a8 8 0 0 1 4.4-3.6A15.7 15.7 0 0 0 8.1 8zM12 20a14 14 0 0 1-1.9-4h3.8A14 14 0 0 1 12 20zm2.3-6H9.7a14.7 14.7 0 0 1 0-4h4.6a14.7 14.7 0 0 1 0 4zm.2 5.6a15.7 15.7 0 0 0 1.4-3.6h3a8 8 0 0 1-4.4 3.6zm1.8-5.6a16.5 16.5 0 0 0 0-4h3.4a8 8 0 0 1 0 4h-3.4z"/></svg>
          www.tovrin.com.au
        </li>
      </ul>
    </div>
  </section>
</main>
</body>
</html>
```